Business card design needed

I need a business card design for a new online retail business based in Australia. I am unsure of the exact content of what I will be selling but it will be probably women's clothing, accessories, gym wear, gifts and maybe homeware linen. I am wanting a classy design that portrays the image of class/style/upmarket.

Target Market(s)

predominantely women - 20-50 age group

Industry/Entity Type

Retail

Contact Information for Business Card

Quietly Golden
Renata Calloway
Director
ABN 73418250964
17 Harrow Crescent Linfield Park NSW 2391
ph: +61 427 905 184
sales@quietlygolden.com.au

Logo Text

I am open for suggestions here

Requirements
Must have
• The design must be both sides of the card

```html
<!DOCTYPE html>
<html lang="en">
<head>
<meta charset="utf-8">
<title>Quietly Golden – Business Card</title>
<link rel="stylesheet" href="https://fonts.googleapis.com/css2?family=Arimo:wght@400&display=swap">
<style>
  :root {
    --stage: #262626;
    --purple: #a2409b;
    --orange: #f08c2c;
    --salmon: #df7b5f;
    --card-light: #f4f4f4;
    --card-shade: #d6d6d6;
    --text-grey: #555555;
    --white: #ffffff;
  }
  * { margin: 0; padding: 0; box-sizing: border-box; }
  html, body {
    width: 1200px;
    height: 900px;
    overflow: hidden;
    background: var(--stage);
    font-family: "Arimo", Arial, sans-serif;
  }
  .canvas { position: relative; width: 1200px; height: 900px; }

  .card {
    position: absolute;
    width: 600px;
    height: 343px;
    overflow: hidden;
    background: var(--card-light);
  }
  .card--front { left: 110px; top: 70px; }
  .card--back  { left: 490px; top: 480px; }

  .card-art { position: absolute; inset: 0; width: 100%; height: 100%; }

  .front-wordmark {
    position: absolute;
    left: 0; right: 0;
    top: 190px;
    text-align: center;
    font-size: 38px;
    color: var(--purple);
    font-weight: 400;
  }

  .back-band {
    position: absolute;
    left: 0; top: 0; bottom: 0;
    width: 178px;
    background: linear-gradient(180deg, var(--salmon) 0%, #c65a82 45%, var(--purple) 75%, var(--purple) 100%);
  }
  .back-wordmark {
    position: absolute;
    left: 0; right: 0;
    bottom: 40px;
    text-align: center;
    color: var(--white);
    font-size: 19px;
    font-weight: 400;
  }
  .back-decor {
    position: absolute;
    right: -40px; top: -20px;
    width: 300px; height: 300px;
    border-radius: 50%;
    background: #e9e9e9;
  }
  .back-details {
    position: absolute;
    left: 212px; top: 48px; right: 20px; bottom: 24px;
    color: var(--text-grey);
  }
  .person-name { font-size: 22px; color: var(--purple); }
  .person-role { font-size: 13px; margin-top: 12px; }
  .address { position: absolute; top: 172px; font-size: 14px; line-height: 1.35; }
  .contact-list { position: absolute; top: 232px; list-style: none; font-size: 14px; }
  .contact-list li { display: flex; align-items: center; gap: 8px; margin-bottom: 6px; }
  .contact-icon { width: 12px; height: 12px; fill: var(--purple); flex: none; }
</style>
</head>
<body>
<main class="canvas">

  <section class="card card--front" aria-label="Business card front">
    <svg class="card-art" viewBox="0 0 600 343" aria-hidden="true">
      <defs>
        <linearGradient id="frontBase" x1="0" y1="0" x2="0" y2="1">
          <stop offset="0" stop-color="#a2409b"/>
          <stop offset="1" stop-color="#f08c2c"/>
        </linearGradient>
        <linearGradient id="frontCorner" x1="0" y1="0" x2="1" y2="0">
          <stop offset="0" stop-color="#e0835a"/>
          <stop offset="1" stop-color="#c7607c"/>
        </linearGradient>
        <radialGradient id="frontOval" cx="0.5" cy="0.45" r="0.6">
          <stop offset="0" stop-color="#ffffff"/>
          <stop offset="0.6" stop-color="#f1f1f1"/>
          <stop offset="1" stop-color="#d4d4d4"/>
        </radialGradient>
      </defs>
      <rect width="600" height="343" fill="url(#frontBase)"/>
      <rect width="300" height="343" fill="url(#frontCorner)"/>
      <ellipse cx="285" cy="205" rx="305" ry="230" fill="#ffffff"/>
      <ellipse cx="285" cy="205" rx="294" ry="220" fill="url(#frontOval)"/>
    </svg>
    <p class="front-wordmark">Quietly Golden</p>
  </section>

  <section class="card card--back" aria-label="Business card back">
    <div class="back-decor" aria-hidden="true"></div>
    <div class="back-band">
      <p class="back-wordmark">Quietly Golden</p>
    </div>
    <div class="back-details">
      <h1 class="person-name" style="font-weight:400">Renata Calloway</h1>
      <p class="person-role">Director</p>
      <p class="address">ABN 73418250964 17 Harrow Crescent<br>Linfield Park NSW 2391</p>
      <ul class="contact-list">
        <li>
          <svg class="contact-icon" viewBox="0 0 24 24" aria-hidden="true"><path d="M6.6 10.8a15.1 15.1 0 0 0 6.6 6.6l2.2-2.2c.3-.3.7-.4 1-.2 1.1.4 2.3.6 3.6.6.6 0 1 .4 1 1V20c0 .6-.4 1-1 1A17 17 0 0 1 3 4c0-.6.4-1 1-1h3.5c.6 0 1 .4 1 1 0 1.3.2 2.5.6 3.6.1.3 0 .7-.2 1z"/></svg>
          <span>+61 427 905 184</span>
        </li>
        <li>
          <svg class="contact-icon" viewBox="0 0 24 24" aria-hidden="true"><path d="M2 5h20v14H2z M2 5l10 8 10-8" fill="#a2409b" stroke="#ffffff" stroke-width="1.5"/></svg>
          <span>sales@quietlygolden.com.au</span>
        </li>
      </ul>
    </div>
  </section>

</main>
</body>
</html>
```